Lanternfield Drinks business cards

We need a business card design for our new logo. The company is modern, progressive, professional, yet approachable. The key products are ready to drink bottles and cans of coffee based beverages.
These cards will be a critical part of the first impression made by our sales organization, business development team, and all external facing personnel.
Card can be a vertical or horizontal orientation.

Target Market(s)

Customers, suppliers, business partners

Industry/Entity Type

Business

Contact Information for Business Card

Business cards should feature Company Name and Logo.

Font styles to use
Serif

Colors

Designer to choose colors to be used in the design.

Requirements
Must have
• Strong readability of Name, phone #, mobile number and email address.
• Job title, website url, Street Address, and other details can be secondary level readability.
Nice to have
• High impact, simplistic quality design.
• Ok to utilize the 'H in the box' separate from the company name

```html
<!DOCTYPE html>
<html lang="en">
<head>
<meta charset="utf-8">
<title>Lanternfield Drinks Business Cards</title>
<link rel="stylesheet" href="https://fonts.googleapis.com/css2?family=Crimson+Pro:ital,wght@0,400;0,600;0,700;1,700&display=swap">
<style>
  :root {
    --backdrop: #3a3a3c;
    --card: #232325;
    --orange: #e8582b;
    --amber: #e79a2c;
    --ink-light: #f2f2f2;
  }
  * { box-sizing: border-box; margin: 0; padding: 0; }
  html, body { width: 799px; height: 1200px; overflow: hidden; }
  body {
    background: var(--backdrop);
    font-family: "Crimson Pro", Georgia, serif;
    display: flex; flex-direction: column; align-items: center; justify-content: space-around;
    padding: 40px 0;
  }
  .card {
    position: relative;
    width: 660px; height: 377px;
    background: var(--card);
    border-radius: 4px;
    box-shadow: 0 14px 30px rgba(0,0,0,.45);
  }
  .brand { position: absolute; text-align: center; }
  .brand-square {
    display: block; margin: 0 auto 12px;
    width: 58px; height: 58px; border: 4px solid var(--orange);
  }
  .brand-name {
    color: var(--orange); font-weight: 600; text-transform: uppercase;
    letter-spacing: 1px; line-height: 1; white-space: nowrap;
  }
  .brand-rule { display: block; height: 2px; background: var(--amber); margin-top: 8px; }
  .card-front .brand { left: 50%; top: 78px; transform: translateX(-50%); }
  .card-front .brand-name { font-size: 44px; }
  .website {
    position: absolute; left: 0; right: 0; top: 268px;
    display: flex; align-items: center; justify-content: center; gap: 18px;
    color: var(--ink-light); font-size: 22px; letter-spacing: .5px;
  }
  .website .domain { color: var(--orange); }
  .website .dash { width: 50px; height: 5px; background: var(--orange); border-radius: 3px; }
  .holder { position: absolute; left: 40px; top: 34px; }
  .holder-name { color: var(--orange); font-size: 26px; font-weight: 700; font-style: italic; }
  .holder-title { color: var(--ink-light); font-size: 15px; }
  .contacts { position: absolute; left: 40px; top: 200px; list-style: none; color: var(--ink-light); font-size: 17px; }
  .contacts li { display: flex; align-items: center; gap: 12px; line-height: 24px; }
  .contacts svg { width: 14px; height: 14px; fill: var(--orange); }
  .contacts .address { font-size: 18px; margin-top: 2px; }
  .card-back .brand { right: 40px; top: 150px; }
  .card-back .brand-square { width: 48px; height: 48px; }
  .card-back .brand-name { font-size: 32px; }
</style>
</head>
<body>
  <section class="card card-front">
    <div class="brand">
      <span class="brand-square"></span>
      <p class="brand-name">Lanternfield Drinks</p>
      <span class="brand-rule"></span>
    </div>
    <p class="website"><span class="dash"></span><span>www.<span class="domain">lanternfielddrinks</span>.com</span><span class="dash"></span></p>
  </section>

  <section class="card card-back">
    <div class="holder">
      <p class="holder-name">John Doe Smith</p>
      <p class="holder-title">Managing Director</p>
    </div>
    <ul class="contacts">
      <li><svg viewBox="0 0 16 16"><path d="M3 2h3l1 4-2 1a9 9 0 0 0 4 4l1-2 4 1v3c0 1-1 1-2 1A12 12 0 0 1 2 4c0-1 0-2 1-2z"/></svg>555.555.5555</li>
      <li><svg viewBox="0 0 16 16"><path d="M4 1h8v14H4zM6 3v9h4V3z"/></svg>666.666.7777</li>
      <li><svg viewBox="0 0 16 16"><path d="M1 3h14v10H1zM2 4l6 5 6-5z"/></svg>johndoe@yourwebsite.com</li>
      <li><svg viewBox="0 0 16 16"><path d="M8 1a7 7 0 1 0 0 14A7 7 0 0 0 8 1zm0 2c1 1 2 3 2 5s-1 4-2 5c-1-1-2-3-2-5s1-4 2-5zM2 8h12v1H2z"/></svg>www.yourwebsite.com</li>
      <li class="address">234 Anywhere St., Any Town, US 123456</li>
    </ul>
    <div class="brand">
      <span class="brand-square"></span>
      <p class="brand-name">Lanternfield Drinks</p>
      <span class="brand-rule"></span>
    </div>
  </section>
</body>
</html>
```